Recruitment of Luzara Manpower for the UK market

I want a website for the UK market to attract businesses and companies to come to us for Philipine labour. We want an information site that gives all information on what we do and how we can recruit Philippine labour.
This is a recruitment site for companies to contact us with their requirements for skilled workers coming from the Philipines over to the UK to work.

Target Market(s)

Uk Companies and businesses who want Philipine skilled workers

Industry/Entity Type

REcruitment

Coding

Number of Pages Required

5+ page

Font styles to use
Sans Serif

Colors
0054AA
0677BA
7BADD7
CADEEF
E8F1F8
0094D4
00A9DD
6FCCEA
C7EBF8
E9F6FB
EE7325
F08F49
F5BC92
FAE3D3
FDF4ED
EB3D1F
EC4F4E
F09395
F8D3D4
FCEDEE

Requirements
Must have
• Look professional and corperate with drop down menus for Home ,about, services,articles. training , contact us
Nice to have
• Look at Velmora recruitment- https://velmorarecruitment.example.co.uk/. This is my current site - https://www.trellanstaffing.example.com/
Should not have
• Cartoons or silly pictures , needs to be corperate looking

```html
<!DOCTYPE html>
<html lang="en">
<head>
<meta charset="utf-8">
<title>Luzara Manpower – Skilled Philippine Workers for UK Companies</title>
<link href="https://fonts.googleapis.com/css2?family=Roboto:wght@400;500;700&family=Roboto+Condensed:wght@400;700&display=swap" rel="stylesheet">
<style>
:root{
  --red:#EC4F4E;
  --red-deep:#E2403F;
  --red-soft:#F09395;
  --ink:#1b1b1b;
  --body:#444;
  --muted:#777;
  --line:#d9d9d9;
  --map:#88A9F2;
  --navy:#1f3f8f;
  --white:#fff;
}
*{box-sizing:border-box;margin:0;padding:0}
html,body{width:1200px;height:3882px;overflow:hidden;background:var(--white)}
body{position:relative;font-family:"Roboto",Arial,sans-serif;color:var(--ink)}
.abs{position:absolute}
a{color:inherit}

/* header */
.site-header{left:0;top:0;width:1200px;height:78px;background:var(--white)}
.brand{left:99px;top:22px;font-size:24px;font-weight:700;color:var(--red);display:flex;align-items:center;gap:8px}
.brand-dot{width:14px;height:14px;background:var(--red);border-radius:50%}
.main-nav{right:96px;top:24px;display:flex;gap:14px;font-size:16px}
.main-nav span{padding:5px 15px;border-radius:4px;color:#333}
.main-nav .active{background:var(--red);color:var(--white)}

/* hero */
.hero-photo{left:0;top:78px;width:1200px;height:603px;background:linear-gradient(120deg,#5a3a35 0%,#8c6a5c 35%,#b9b7ba 60%,#6e7fa0 80%,#3a4a6a 100%)}
.hero-card{left:66px;top:130px;width:389px;height:518px;background:var(--white);border-radius:6px;box-shadow:0 4px 18px rgba(0,0,0,.2)}
.hero-card h2{position:absolute;left:62px;top:18px;font-size:33px;font-weight:500;font-family:"Roboto",sans-serif}
.ribbon{left:57px;top:197px;width:437px;height:67px}
.ribbon span{position:absolute;left:104px;top:12px;font-size:33px;color:var(--white);font-family:"Roboto",sans-serif}
.field{position:absolute;border:1.5px solid #d6d6d6;background:var(--white);font-size:12px;color:#999;padding:14px 10px}
.send-btn{position:absolute;left:20px;top:456px;width:350px;height:46px;background:var(--red);color:var(--white);font-size:20px;text-align:center;line-height:46px}
.hero-banner{left:543px;top:505px;width:657px;height:219px;background:var(--red);color:var(--white);padding:26px 0 0 43px;font-family:"Roboto Condensed",sans-serif;font-weight:700;font-size:44px;line-height:54px}

/* services */
.services-title{left:97px;top:800px;font-family:"Roboto Condensed",sans-serif;font-weight:700;font-size:45px;color:var(--red)}
.services-kicker{left:395px;top:818px;font-size:16px;color:#333}
.services-intro{left:396px;top:845px;width:670px;font-size:16px;line-height:26px;color:var(--muted)}
.service-card{top:945px;width:242px;height:461px;border:1.5px solid var(--line);padding:20px 18px}
.service-icon{width:54px;height:54px;background:#e4e4e4;border-radius:6px}
.service-card h3{margin-top:18px;font-size:20px;font-weight:500;font-family:"Roboto",sans-serif}
.service-card p{margin-top:16px;font-size:14px;line-height:21.5px;color:#333}

/* map + contact */
.map-band{left:0;top:1485px;width:1200px;height:558px;background:linear-gradient(90deg,var(--map) 0%,#8fb0f2 30%,#a9c89a 38%,#8fb0f2 50%,var(--map) 100%)}
.contact-box{left:776px;top:1553px;width:308px;height:454px;background:var(--white);border:2px solid var(--navy);border-top:5px solid #1f55b0;padding:14px 20px}
.contact-box h2{text-align:center;font-size:32px;font-weight:500;margin-top:6px}
.contact-row{display:flex;gap:16px;padding:22px 0 12px 14px;border-bottom:1.5px solid #e2e2e2}
.contact-row:last-of-type{border-bottom:none}
.contact-row b{display:block;font-size:16px;font-weight:500;color:var(--navy)}
.contact-row span{font-size:14.5px;color:var(--navy);line-height:22px}
.contact-row .sc{font-variant:small-caps}
.submit-btn{display:block;margin:22px auto 0;width:156px;height:52px;background:var(--red);color:var(--white);font-size:16px;text-align:center;line-height:52px}

/* blog */
.blog-title{left:99px;top:2345px;font-size:44px;font-weight:700;line-height:54px}
.blog-all{left:101px;top:2470px;font-size:16px;color:var(--red);text-decoration:underline}
.post-title{left:512px;font-size:25px;font-weight:700;line-height:34px;width:240px}
.post-more{left:515px;font-size:16px;color:var(--red);text-decoration:underline}
.post-text{left:761px;width:340px;font-size:15px;line-height:25.6px;color:var(--muted)}
.post-divider{left:516px;width:586px;height:1.5px;background:var(--line)}
.bullet{display:inline-block;width:10px;height:10px;border-radius:50%;background:var(--red);margin:0 8px 0 4px}

/* business */
.business-band{left:0;top:2896px;width:1200px;height:425px;background:linear-gradient(90deg,#E94848,var(--red) 60%,#E75856)}
.business-photo{left:118px;top:2950px;width:447px;height:499px;border-bottom-right-radius:260px 280px;background:linear-gradient(160deg,#c9d2e0 0%,#3e56a8 35%,#27305a 70%,#8a8a8a 100%)}
.business-title{left:623px;top:2962px;font-family:"Roboto Condensed",sans-serif;font-weight:700;font-size:45px;line-height:57px;color:var(--white)}
.business-text{left:626px;top:3094px;width:475px;font-size:15px;line-height:25.6px;color:var(--white)}
.business-btn{left:628px;top:3242px;width:158px;height:52px;background:var(--white);color:#222;font-size:16px;text-align:center;line-height:52px}

/* footer */
.foot-icon{width:60px;height:60px;border-radius:50%;background:var(--red);display:flex;align-items:center;justify-content:center}
.foot-text{font-size:18px;line-height:25px;color:#222}
.quick-title{left:525px;top:3480px;font-size:25px;font-weight:500}
.quick-links{left:529px;top:3522px;font-size:16px;line-height:34.5px;color:#222;list-style:none}
.foot-brand{left:761px;top:3587px;font-size:34px;font-weight:700;color:var(--red);display:flex;align-items:center;gap:12px}
.foot-rule{left:111px;top:3781px;width:1000px;height:1.5px;background:#bbb}
.copyright{left:0;top:3814px;width:1200px;text-align:center;font-size:14px;color:#222}
</style>
</head>
<body>

<header class="site-header abs">
  <div class="brand abs"><span class="brand-dot"></span>Luzara Manpower</div>
  <nav class="main-nav abs">
    <span class="active">Home</span><span>About</span><span>Services</span><span>Articles</span><span>Training</span><span>Contact us</span>
  </nav>
</header>

<section>
  <div class="hero-photo abs" role="img" aria-label="Photo of two engineers in hard hats reviewing plans with a tablet in a factory"></div>
  <div class="hero-card abs">
    <h2>Luzara Manpower</h2>
    <div class="field" style="left:20px;top:154px;width:170px;height:45px">First Name</div>
    <div class="field" style="left:201px;top:154px;width:170px;height:45px">Last Name</div>
    <div class="field" style="left:20px;top:212px;width:350px;height:45px">Email</div>
    <div class="field" style="left:20px;top:270px;width:350px;height:45px">Phone</div>
    <div class="field" style="left:20px;top:328px;width:350px;height:105px">Messages</div>
    <div class="send-btn">Send Messages</div>
  </div>
  <svg class="ribbon abs" width="437" height="67" viewBox="0 0 437 67"><polygon points="0,0 417,0 437,33 417,67 0,67" fill="#EC4F4E"/></svg>
  <div class="abs" style="left:161px;top:207px;font-size:33px;color:#fff">Contact us today</div>
  <div class="hero-banner abs">Recruiting and placing skilled<br>Philippine workers into<br>UK companies</div>
</section>

<section>
  <h2 class="services-title abs">Our Services</h2>
  <div class="services-kicker abs">WORKING TOGETHER</div>
  <p class="services-intro abs">We recruit the finest talent available with our dedicated 200 strong team. Our centres are highlighted in red dots on the map</p>

  <article class="service-card abs" style="left:99px">
    <div class="service-icon" role="img" aria-label="Icon of a worker with a question mark"></div>
    <h3>What we do</h3>
    <p>Our company has been estabilished in the Philippines for over 20 years. We have mainly been recruiting philippine workers for the off shore industry in asia but since brexit and the new rules on skilled workers entering the UK we have been working with UK companies who now have chance to recruit some of the finest hard working talent from the Philippines for their companies</p>
  </article>
  <article class="service-card abs" style="left:354px">
    <div class="service-icon" role="img" aria-label="Icon of a handshake"></div>
    <h3>How we help</h3>
    <p>We work with companies to find skilled workers that meet the UK requirements for Visas and work permits. We guide you through the whole process and deliver highly trained people that add value to your business. We are here to help both the companies and the Philippino people to gain a better standard of living for their families.</p>
  </article>
  <article class="service-card abs" style="left:609px">
    <div class="service-icon" role="img" aria-label="Icon of a lightbulb with gears"></div>
    <h3>Where to start</h3>
    <p>We need to know what your issues are and how we can understand the personnal you require , over what time frame and the number of employees you need. Once this is estabilished we start sourcing workers in the Philippines that meet your criteria while starting the process in the UK to be able to have all the documents in place to deliver your company hard working skilled individuals.</p>
  </article>
  <article class="service-card abs" style="left:864px">
    <div class="service-icon" role="img" aria-label="Icon of a globe with contact symbols"></div>
    <h3>Contact us today</h3>
    <p>Please contact us today with your requirements , this can be care workers ,chef, welders, pipe fitters, caravan cabinet makers, medical workers. The UK list of required skills is extensive and the Philippines offersenglish speaking highly qualified hard working employees. Contact us today and make that first step to a highly motivated , quality skilled workforce.</p>
  </article>
</section>

<section>
  <div class="map-band abs" role="img" aria-label="Map of the Philippines with red dots marking recruitment centres"></div>
  <div class="contact-box abs">
    <h2>Contact Us</h2>
    <div class="contact-row">
      <svg width="16" height="14" viewBox="0 0 16 14" style="margin-top:4px"><rect x="1" y="1" width="14" height="12" fill="none" stroke="#EC4F4E" stroke-width="1.6"/><polyline points="1,2 8,8 15,2" fill="none" stroke="#EC4F4E" stroke-width="1.6"/></svg>
      <div><b>EMAIL</b><span>sales@luzaramanpower.example.com</span></div>
    </div>
    <div class="contact-row">
      <svg width="16" height="16" viewBox="0 0 16 16" style="margin-top:4px"><path d="M8 1a5 5 0 0 1 5 5c0 4-5 9-5 9S3 10 3 6a5 5 0 0 1 5-5z" fill="#EC4F4E"/><circle cx="8" cy="6" r="2" fill="#fff"/></svg>
      <div><b>ADDRESS</b><span class="sc">Larkfield Gardens, Westmere HU99 1<br>United Kingdom</span></div>
    </div>
    <div class="contact-row">
      <svg width="16" height="16" viewBox="0 0 24 24" style="margin-top:4px"><path d="M6.6 10.8a15 15 0 0 0 6.6 6.6l2.2-2.2a1 1 0 0 1 1-.25 11.4 11.4 0 0 0 3.6.57 1 1 0 0 1 1 1V20a1 1 0 0 1-1 1A17 17 0 0 1 3 4a1 1 0 0 1 1-1h3.5a1 1 0 0 1 1 1c0 1.25.2 2.45.57 3.57a1 1 0 0 1-.25 1z" fill="#EC4F4E"/></svg>
      <div><b>PHONE</b><span>+1 480-555-0142</span></div>
    </div>
    <div class="submit-btn">Submit Now</div>
  </div>
</section>

<section>
  <h2 class="blog-title abs">Our Recent<br>Blog Articles</h2>
  <a class="blog-all abs">View All Blog</a>

  <h3 class="post-title abs" style="top:2144px">UK Skilled Workers List</h3>
  <a class="post-more abs" style="top:2222px">Read More</a>
  <p class="post-text abs" style="top:2163px">The UK government since brexit have developed a new system based on points (similar to Australia) when recruiting from outside of the UK. Previuosly EU citizens could work in the UK without any extensive documentation or clarification of skills</p>
  <div class="post-divider abs" style="top:2359px"></div>

  <h3 class="post-title abs" style="top:2393px">Sponsor Licence</h3>
  <a class="post-more abs" style="top:2471px">Read More</a>
  <p class="post-text abs" style="top:2412px">If you have areas of your business that meet the entry requirements of skilled labour your next step is to gain a sponsor licence for your business. There are different types of licences depending on the size of the business.</p>
  <div class="post-divider abs" style="top:2582px"></div>

  <h3 class="post-title abs" style="top:2618px">Recruitment Timeline</h3>
  <a class="post-more abs" style="top:2695px">Read More</a>
  <p class="post-text abs" style="top:2636px">&nbsp;Brief us on the job profiles – this is passed on to our teams in the Philippines.<br><span class="bullet"></span>Our teams in the Philippines source suitable candidates, documentation required for each candidate will be checked and vetted by the Recruitment Team. Once deemed qualified, they will now be assessed by their Technical Interviewer .</p>
</section>

<section>
  <div class="business-band abs"></div>
  <div class="business-photo abs" role="img" aria-label="Photo of a welder in a blue helmet working on a metal pipe"></div>
  <h2 class="business-title abs">What the<br>Business is about</h2>
  <p class="business-text abs">We source skilled workers directly from the Philippines to work in the UK. With offices , training locations and specialist recruiters we can find the highest quality individuals to add value and resources to any UK buisness. We delivery quality based on vast experience over a number of years.</p>
  <div class="business-btn abs">Read More</div>
</section>

<footer>
  <div class="abs" style="left:120px;top:3482px;display:flex;gap:30px">
    <div class="foot-icon"><svg width="22" height="26" viewBox="0 0 16 18"><path d="M8 1a6 6 0 0 1 6 6c0 4.5-6 10-6 10S2 11.5 2 7a6 6 0 0 1 6-6z" fill="#fff"/><circle cx="8" cy="7" r="2.2" fill="#EC4F4E"/></svg></div>
    <div class="foot-text" style="margin-top:0">Larkfield Gardens,<br>Westmere HU99 1<br>United Kingdom</div>
  </div>
  <div class="abs" style="left:124px;top:3569px;display:flex;gap:36px;align-items:center">
    <div class="foot-icon"><svg width="24" height="24" viewBox="0 0 24 24"><path d="M6.6 10.8a15 15 0 0 0 6.6 6.6l2.2-2.2a1 1 0 0 1 1-.25 11.4 11.4 0 0 0 3.6.57 1 1 0 0 1 1 1V20a1 1 0 0 1-1 1A17 17 0 0 1 3 4a1 1 0 0 1 1-1h3.5a1 1 0 0 1 1 1c0 1.25.2 2.45.57 3.57a1 1 0 0 1-.25 1z" fill="#fff"/></svg></div>
    <div class="foot-text">+1 07700 900418</div>
  </div>
  <div class="abs" style="left:129px;top:3654px;display:flex;gap:22px;align-items:center">
    <div class="foot-icon"><svg width="26" height="20" viewBox="0 0 16 14"><rect x="1" y="1" width="14" height="12" rx="1.5" fill="none" stroke="#fff" stroke-width="1.6"/><polyline points="1.5,2.5 8,8 14.5,2.5" fill="none" stroke="#fff" stroke-width="1.6"/></svg></div>
    <div class="foot-text">sales@luzaramanpower.example.com</div>
  </div>

  <h3 class="quick-title abs">Quick Links</h3>
  <ul class="quick-links abs"><li>Home</li><li>About</li><li>Services</li><li>Articles</li><li>Training</li><li>Contact us</li></ul>

  <div class="foot-brand abs"><span class="brand-dot" style="width:18px;height:18px"></span>Luzara Manpower</div>

  <div class="foot-rule abs"></div>
  <div class="copyright abs">© Copyright 2023&nbsp; Luzara Manpower, All Rights Reserved.</div>
</footer>

</body>
</html>
```